Business card design for my company.
I would like the card's background colour to be black. You can also see our web site to get an idea of our brand. https://www.tmwhomecrafting.com.au/
- Name
- Email

```html
<!DOCTYPE html>
<html lang="en">
<head>
<meta charset="utf-8">
<title>TMW Home Crafting – Business Card</title>
<link href="https://fonts.googleapis.com/css2?family=Montserrat:wght@400;700&display=swap" rel="stylesheet">
<style>
  :root {
    --stage: #2b2b2b;
    --card: #1e1e1e;
    --green: #1f9a45;
    --white: #f4f4f4;
    --muted: #d9d9d9;
  }
  html, body {
    margin: 0;
    padding: 0;
    width: 1200px;
    height: 801px;
    overflow: hidden;
    background: var(--stage);
    font-family: "Montserrat", sans-serif;
  }
  .sheet {
    width: 1200px;
    height: 801px;
    display: flex;
    align-items: center;
    justify-content: center;
    gap: 50px;
  }
  .card {
    position: relative;
    width: 535px;
    height: 306px;
    background: var(--card);
    border-radius: 22px;
    box-shadow: 0 14px 30px rgba(0,0,0,0.45);
    overflow: hidden;
  }
  /* front */
  .brand-mark {
    position: absolute;
    top: 40px;
    right: 38px;
    display: flex;
    align-items: center;
    gap: 10px;
    font-weight: 700;
    font-size: 17px;
    letter-spacing: 2px;
    color: var(--white);
  }
  .brand-mark .dot {
    width: 14px;
    height: 14px;
    background: var(--green);
  }
  .divider {
    position: absolute;
    left: 40px;
    right: 40px;
    top: 176px;
    height: 1px;
    background: var(--green);
  }
  .identity {
    position: absolute;
    left: 40px;
    top: 118px;
  }
  .identity .name {
    margin: 0;
    font-weight: 700;
    font-size: 24px;
    letter-spacing: 0.5px;
    color: var(--green);
    text-transform: uppercase;
  }
  .identity .role {
    margin: 2px 0 0;
    font-size: 14px;
    color: var(--white);
  }
  .contacts {
    position: absolute;
    left: 40px;
    top: 194px;
    margin: 0;
    padding: 0;
    list-style: none;
  }
  .contacts li {
    display: flex;
    align-items: center;
    gap: 10px;
    font-size: 14px;
    color: var(--muted);
    line-height: 28px;
  }
  .contacts svg { width: 13px; height: 13px; fill: var(--green); }
  /* back */
  .card-back {
    display: flex;
    align-items: center;
    justify-content: center;
  }
  .brand-lockup {
    display: flex;
    align-items: center;
    gap: 16px;
    font-weight: 700;
    font-size: 30px;
    letter-spacing: 3px;
    color: var(--white);
  }
  .brand-lockup .dot {
    width: 22px;
    height: 22px;
    background: var(--green);
  }
</style>
</head>
<body>
<main class="sheet">
  <section class="card card-front">
    <div class="brand-mark"><span class="dot"></span>TMW HOME CRAFTING</div>
    <div class="identity">
      <h1 class="name">Dana Whitfield</h1>
      <p class="role">CEO/Founder</p>
    </div>
    <div class="divider"></div>
    <ul class="contacts">
      <li>
        <svg viewBox="0 0 24 24" aria-hidden="true"><path d="M6.6 10.8a15.1 15.1 0 0 0 6.6 6.6l2.2-2.2a1 1 0 0 1 1-.25 11.4 11.4 0 0 0 3.6.57 1 1 0 0 1 1 1V20a1 1 0 0 1-1 1A17 17 0 0 1 3 4a1 1 0 0 1 1-1h3.5a1 1 0 0 1 1 1c0 1.25.2 2.45.57 3.6a1 1 0 0 1-.25 1z"/></svg>
        555-204-7183
      </li>
      <li>
        <svg viewBox="0 0 24 24" aria-hidden="true"><path d="M2 5h20v14H2z M2 5l10 8 10-8" fill="var(--green)"/><path d="M2 5l10 8 10-8" fill="none" stroke="var(--card)" stroke-width="2"/></svg>
        info@tmwhomecrafting.com.au
      </li>
      <li>
        <svg viewBox="0 0 24 24" aria-hidden="true"><circle cx="12" cy="12" r="10"/><path d="M2 12h20M12 2c3 3 3 17 0 20M12 2c-3 3-3 17 0 20" fill="none" stroke="var(--card)" stroke-width="1.5"/></svg>
        www.tmwhomecrafting.com.au
      </li>
    </ul>
  </section>

  <section class="card card-back">
    <div class="brand-lockup"><span class="dot"></span>TMW HOME CRAFTING</div>
  </section>
</main>
</body>
</html>
```